We need a wordpress design that will incorporate a professional color scheme with company logo in a clean layout. The design needs to consider that this will be developed on a responsive theme. Colors are blue and green of the logo and and an accent color (perhaps very light brown/tan). Client wants a 'modern' look.

Industry/Entity Type

It Company

Font styles to use
Serif
Sans Serif

Colors

Designer to choose colors to be used in the design.

Requirements
Must have
• navigation: 1) Home; 2) Services; 3) Auctions by Type; 4) About Us; 5) QVT Bulletin 6) Videos; 7) Contact Us

VERY general idea of layout is attached, Site will have slideshow, image is attached. Widgets used to are: 1) Email Contact Form; 2) social media icons, QT Linkora, ViewNest; 3) Featured Auctions; 4) News & Events blog; Featured Video

Footer will have affiliation logos, contact info and perhaps smaller company logo:
Phone: (512) 555-0147 / Mobile: (512) 555-0183 (Miriam)
Email: mdorrance482@mailbox-example.com / holden@parkelldorrance.example
Address: 417 FM 1382N • #B208 • PMB315 • Austin, TX 78791

Nice to have
• Use of a dropdown menu

```html
<!DOCTYPE html>
<html lang="en">
<head>
<meta charset="utf-8">
<title>Parkell Dorrance Auction Marketing</title>
<link href="https://fonts.googleapis.com/css2?family=Ubuntu:wght@400;500;700&family=Arimo:wght@400;700&family=PT+Sans:wght@400;700&display=swap" rel="stylesheet">
<style>
:root{
  --tan:#b8946a;
  --green:#0f9150;
  --blue:#1a63ad;
  --blue-dark:#0c4d8f;
  --navy:#0f4f94;
  --panel:#ddd2bb;
  --side:#efefef;
  --ink:#1b1b1b;
  --muted:#333;
}
*{margin:0;padding:0;box-sizing:border-box}
html,body{width:822px;height:1200px;overflow:hidden;background:var(--tan)}
body{font-family:"Arimo",Arial,sans-serif;color:var(--ink);position:relative}
.page{position:absolute;left:69px;top:12px;width:685px;height:1172px;background:#fff}
.header{position:absolute;left:0;top:0;width:685px;height:102px;background:linear-gradient(#fff,#e4e4e4)}
.brand{position:absolute;left:18px;top:14px;display:flex;align-items:center;gap:8px}
.brand-mark{width:22px;height:22px;border-radius:50%;background:var(--green)}
.brand-name{font-family:"Ubuntu",sans-serif;font-weight:700;color:var(--navy);font-size:16px;line-height:18px}
.social{position:absolute;left:362px;top:50px;display:flex;gap:7px}
.social span{width:24px;height:24px;border-radius:50%;background:var(--blue);color:#fff;font-size:7px;font-weight:700;display:flex;align-items:center;justify-content:center}
.contact{position:absolute;right:15px;top:42px;text-align:right;font-size:12px;line-height:19px}
.contact .phone{font-weight:500;display:flex;align-items:center;gap:5px;justify-content:flex-end}
.contact .mail{font-size:10px;text-decoration:underline;display:flex;align-items:center;gap:5px;justify-content:flex-end}
.nav{position:absolute;left:0;top:102px;width:685px;height:35px;background:var(--green);display:flex}
.nav a{color:#fff;font-family:"Ubuntu",sans-serif;font-weight:500;font-size:11px;white-space:nowrap;text-decoration:none;display:flex;align-items:center;justify-content:center;border-right:1px solid rgba(255,255,255,.25)}
.nav a:last-child{border-right:0}
.dropdown{position:absolute;left:183px;top:138px;width:113px;z-index:3}
.dropdown a{display:block;height:22px;line-height:22px;padding-left:12px;background:var(--green);color:#fff;font-size:9.5px;font-weight:700;white-space:nowrap;overflow:hidden;border:1px solid #5fb88a;border-top:0;text-decoration:none}
.dropdown a.active{background:#a0876a}
.hero{position:absolute;left:0;top:136px;width:685px;height:250px;background:linear-gradient(180deg,#6f9ab8 0%,#8aa77f 35%,#b5782f 60%,#6a5b3f 100%)}
.hero-caption{position:absolute;left:236px;top:161px;width:434px;height:64px;background:rgba(229,204,165,.9);display:flex;align-items:center;padding-left:14px}
.hero-caption p{font-family:"PT Sans",sans-serif;font-size:20px;line-height:25px;color:#222;width:290px;white-space:nowrap}
.btn-learn{margin-left:8px;background:var(--blue-dark);color:#fff;font-family:"PT Sans",sans-serif;font-size:17px;white-space:nowrap;padding:6px 11px;border-radius:6px;border:1px solid #6b9ad3}
.welcome{position:absolute;left:18px;top:406px;width:430px}
.welcome h1{font-family:"Ubuntu",sans-serif;font-weight:500;font-size:17px;margin-bottom:8px;white-space:nowrap}
.welcome p{font-size:10px;line-height:16px;color:var(--muted)}
.listing{position:absolute;left:15px;width:432px;height:227px;background:var(--panel);border:1px solid #c8bca3}
.listing h2{height:31px;background:linear-gradient(#2d7fcc,var(--blue-dark));border-radius:6px 6px 0 0;color:#fff;font-weight:400;font-size:12px;line-height:32px;padding-left:12px;margin:-1px -1px 0}
.thumb{position:absolute;left:25px;top:40px;width:110px;height:73px;border:2px solid #444;background:linear-gradient(#a9c4de,#9b6c52 60%,#3d7d3a)}
.btn{position:absolute;left:50px;width:70px;height:23px;background:var(--blue);border-radius:3px;color:#fff;font-size:9.5px;line-height:23px;padding-left:8px;display:flex;align-items:center;gap:6px}
.btn i{width:12px;height:10px;background:#dfe9f5;border-radius:2px;display:inline-block}
.info{position:absolute;left:155px;top:42px;width:260px;font-family:"PT Sans",sans-serif;font-size:9px;line-height:13px}
.info .date{font-weight:700;font-size:10px;letter-spacing:.3px}
.info .sale{margin-top:19px;text-transform:uppercase;font-size:9px;line-height:12px}
.info .live{margin-top:24px}
.info b{letter-spacing:.3px}
.pin{display:inline-block;width:7px;height:9px;vertical-align:-1px;margin-right:3px}
.powered{position:absolute;left:233px;top:994px;width:131px;height:41px;border:1px solid #bbb;border-radius:5px;font-size:7px;color:var(--navy);padding:5px 8px}
.powered strong{display:block;font-size:11px;color:var(--navy)}
.side-box{position:absolute;left:468px;width:202px;background:var(--side);border:1px solid #ddd}
.side-box h3{height:28px;background:var(--green);color:#fff;font-family:"Ubuntu",sans-serif;font-weight:500;font-size:15px;line-height:29px;padding-left:12px;text-align:left}
.featured{top:420px;height:208px;text-align:center;font-size:9px;line-height:11px}
.featured .photo{width:173px;height:74px;margin:9px auto 12px;border:2px solid #555;background:linear-gradient(#b9cfe1,#9aa98b 50%,#4f6b3d)}
.video{position:absolute;left:468px;top:654px;width:202px;height:136px;background:linear-gradient(#c9d6e2,#9c9782 60%,#53733f);border:1px solid #999}
.video .bar{position:absolute;left:0;bottom:0;width:100%;height:12px;background:#111}
.news{top:820px;height:206px}
.news ul{list-style:none;padding:20px 16px 0 16px;font-size:8.5px;line-height:11px;color:#333}
.news li{margin-bottom:9px}
.footer{position:absolute;left:0;top:1058px;width:685px;height:114px;background:var(--navy);color:#fff}
.footer-info{position:absolute;left:18px;top:22px;font-size:9.2px;line-height:15.2px}
.footer-brand{position:absolute;left:421px;top:34px;display:flex;align-items:center;gap:6px}
.footer-brand .brand-name{color:#fff;font-size:12px;line-height:14px}
.badges{position:absolute;left:557px;top:20px;display:grid;grid-template-columns:40px 60px;gap:10px 8px}
.badges span{height:34px;background:#d9e3ef;opacity:.85}
.badges span.round{border-radius:50%;width:34px}
</style>
</head>
<body>
<div class="page">
  <header class="header">
    <div class="brand">
      <span class="brand-mark"></span>
      <div class="brand-name">Parkell Dorrance<br>Auction Marketing</div>
    </div>
    <div class="social">
      <span>QT</span><span>VN</span><span>Lk</span>
    </div>
    <div class="contact">
      <div class="phone"><svg width="11" height="11" viewBox="0 0 24 24"><path fill="#0f9150" d="M6.6 10.8a15 15 0 0 0 6.6 6.6l2.2-2.2c.3-.3.7-.4 1-.2 1.1.4 2.3.6 3.6.6.6 0 1 .4 1 1V20c0 .6-.4 1-1 1A17 17 0 0 1 3 4c0-.6.4-1 1-1h3.5c.6 0 1 .4 1 1 0 1.3.2 2.5.6 3.6.1.3 0 .7-.2 1z"/></svg>(512) 555-0147, (512) 555-0183</div>
      <div class="mail"><svg width="14" height="10" viewBox="0 0 14 10"><rect width="14" height="10" fill="#0f9150"/><path d="M0 0l7 5 7-5" stroke="#fff" fill="none"/></svg>mdorrance482@mailbox-example.com</div>
    </div>
  </header>

  <nav class="nav">
    <a style="width:83px">HOME</a>
    <a style="width:98px">SERVICES</a>
    <a style="width:112px">AUCTIONS BY TYPE</a>
    <a style="width:105px">ABOUT US</a>
    <a style="width:110px">QVT BULLETIN</a>
    <a style="width:76px">VIDEOS</a>
    <a style="width:101px">CONTACT US</a>
  </nav>

  <section class="hero" role="img" aria-label="Photo of a two-storey wooden family house at dusk among pine trees">
    <div class="hero-caption">
      <p>Making "SOLD" Our Specialty<br>for 30 Years</p>
      <span class="btn-learn">Learn More</span>
    </div>
  </section>

  <div class="dropdown">
    <a>Real Estate</a>
    <a class="active">Business Liquiations</a>
    <a>Commercial</a>
    <a>Appraisal</a>
  </div>

  <section class="welcome">
    <h1>Welcome to parkell dorrance auction Marketing</h1>
    <p>Parkell dorrance Aauction And Marketing have offered our services to our clients as a versatile Auction Company with the ability to perform a variety of Auction types.</p>
  </section>

  <article class="listing" style="top:484px">
    <h2>2280 LARKSPUR LANE, BLAKELY, GA</h2>
    <div class="thumb" role="img" aria-label="Photo of a brick two-storey house with garage"></div>
    <div class="btn" style="top:128px"><i></i>Details</div>
    <div class="btn" style="top:159px"><i></i>Photos</div>
    <div class="info">
      <div class="date">THURSDAY, AUGUST 21ST AT10:00 A.M.</div>
      <div class="sale">Selling 3120 acres of land in tracts of 2590 acres &amp; 560 acres</div>
      <div class="live"><b>LIVE OFF-SITE AUCTION</b><br><b>Auction Location:</b><br>
      <svg class="pin" viewBox="0 0 10 13"><path fill="#d11" d="M5 0a5 5 0 0 1 5 5c0 3-5 8-5 8S0 8 0 5a5 5 0 0 1 5-5z"/></svg>118 N Elm Row, Laverne, OK 73890<br><b>Property Location:</b><br>
      <svg class="pin" viewBox="0 0 10 13"><path fill="#d11" d="M5 0a5 5 0 0 1 5 5c0 3-5 8-5 8S0 8 0 5a5 5 0 0 1 5-5z"/></svg>118 N Elm Row, Laverne, OK 73890<br><b>Begins:</b>&nbsp; 08/21/14 at 10:00 AM CDT</div>
    </div>
  </article>

  <article class="listing" style="top:738px">
    <h2>2280 LARKSPUR LANE, BLAKELY, GA</h2>
    <div class="thumb" role="img" aria-label="Photo of a brick two-storey house with garage"></div>
    <div class="btn" style="top:128px"><i></i>Details</div>
    <div class="btn" style="top:159px"><i></i>Photos</div>
    <div class="info">
      <div class="date">THURSDAY, AUGUST 21ST AT10:00 A.M.</div>
      <div class="sale">Selling 3120 acres of land in tracts of 2590 acres &amp; 560 acres</div>
      <div class="live"><b>LIVE OFF-SITE AUCTION</b><br><b>Auction Location:</b><br>
      <svg class="pin" viewBox="0 0 10 13"><path fill="#d11" d="M5 0a5 5 0 0 1 5 5c0 3-5 8-5 8S0 8 0 5a5 5 0 0 1 5-5z"/></svg>118 N Elm Row, Laverne, OK 73890<br><b>Property Location:</b><br>
      <svg class="pin" viewBox="0 0 10 13"><path fill="#d11" d="M5 0a5 5 0 0 1 5 5c0 3-5 8-5 8S0 8 0 5a5 5 0 0 1 5-5z"/></svg>118 N Elm Row, Laverne, OK 73890<br><b>Begins:</b>&nbsp; 08/21/14 at 10:00 AM CDT</div>
    </div>
  </article>

  <div class="powered">powered by:<strong>BidWorks Hub</strong>Powering the auction trade</div>

  <aside class="side-box featured">
    <h3>Featured Acutions</h3>
    <p style="margin-top:14px">13.35 ACRES OF PRIME DEVELOP<br>&amp; 33RD STREET</p>
    <div class="photo" role="img" aria-label="Photo of a crowd gathered outside a house at an auction"></div>
    <p>LOTS 13 &amp; 14 FOR SALE, HOUGHTON<br>IOWA<br>Fourth Street, Houghton, IA 52690</p>
  </aside>

  <div class="video" role="img" aria-label="Featured video still of a grey two-storey house with porch">
    <svg style="position:absolute;left:82px;top:38px" width="38" height="38" viewBox="0 0 38 38"><circle cx="19" cy="19" r="19" fill="rgba(0,0,0,.65)"/><path d="M15 11l12 8-12 8z" fill="#fff"/></svg>
    <div class="bar"></div>
  </div>

  <aside class="side-box news">
    <h3>News &amp; Events</h3>
    <ul>
      <li>Great Land Auction Companies Make All the Difference</li>
      <li>Great OK Farms for Sale at Auction Prices</li>
      <li>Farmland Auctions on Route 66</li>
      <li>Great Land Auction Companies Make All the Difference</li>
      <li>Great OK Farms for Sale at Auction Prices</li>
    </ul>
  </aside>

  <footer class="footer">
    <div class="footer-info">
      Phone: (512) 555-0147 / Mobile: (512) 555-0183 (Miriam)<br>
      Email: mdorrance482@mailbox-example.com / holden@parkelldorrance.example<br>
      Address: 417 FM 1382N • #B208 • PMB315 • Austin, TX 78791<br>
      Copyright © 2005 - 2014: Parkell Dorrance Auction Marketing, Inc.<br>
      All Rights Reserved • Powered by: BidWorks Hub and CountryBidList
    </div>
    <div class="footer-brand">
      <span class="brand-mark" style="width:14px;height:14px"></span>
      <div class="brand-name">Parkell Dorrance<br>Auction Marketing</div>
    </div>
    <div class="badges">
      <span class="round"></span><span></span>
      <span class="round"></span><span></span>
    </div>
  </footer>
</div>
</body>
</html>
```